Concierge Dental / Medical Supply Ordering Business - Sleek, Efficient, Professional, Elite

www.brantonkeelmedical.com - example website.

We are a concierge supply ordering business for medical and dental that provide DSO price savings on supplies while maintaining business autonomy and independence.

We want a very simple website that looks very professional says what we do and gives a very simple method to contact us & sign up as above.

Target Market(s)

Independent Dental and Medical Practices

Industry/Entity Type

Dental and Medical - healthcare

Coding

Coded - Design and coding required

Number of Pages Required

3 page

Font styles to use
Sans Serif

Colors
0054AA
0677BA
7BADD7
CADEEF
E8F1F8

Requirements
Must have
• Simple contact page, sleek efficient design, uncomplicated.
Nice to have
• Sign up page vs just a contact page.
Should not have
• Lots of pages, hard to navigate,

```html
<!DOCTYPE html>
<html lang="en">
<head>
<meta charset="utf-8">
<title>Keelpoint Dental Supply</title>
<link href="https://fonts.googleapis.com/css2?family=Poppins:wght@500;600;700&family=Lato:wght@400;700&display=swap" rel="stylesheet">
<style>
:root{
  --navy:#0054AA;
  --blue:#0677BA;
  --sky:#7BADD7;
  --pale:#CADEEF;
  --mist:#E8F1F8;
  --ink:#222;
  --grey:#666;
  --footer:#0e0e10;
}
*{box-sizing:border-box;margin:0;padding:0}
html,body{width:1200px;height:3956px;overflow:hidden;background:#fff}
body{font-family:"Lato",sans-serif;color:var(--ink);position:relative}
h1,h2,h3,.btn,.brand{font-family:"Poppins",sans-serif}
section,header,footer{position:absolute;left:0;width:1200px}
.abs{position:absolute}
.btn{position:absolute;display:flex;align-items:center;justify-content:center;color:#fff;font-weight:700;font-size:15px;border-radius:6px;background:linear-gradient(90deg,var(--blue),var(--navy))}
.mark{display:block;width:28px;height:28px;border-radius:5px;background:var(--sky);border:3px solid var(--pale)}
.center{left:0;right:0;text-align:center}
.center .mark{margin:0 auto}

/* hero */
.hero{top:0;height:685px;background:linear-gradient(120deg,#6f9cc8 0%,#3f78b4 40%,#2a5f9e 70%,#7aa6cf 100%)}
.hero-photo{position:absolute;inset:0;background:radial-gradient(circle at 72% 30%,rgba(232,241,248,.35),transparent 45%),radial-gradient(circle at 25% 20%,rgba(202,222,239,.3),transparent 40%)}
.nav{top:0;height:115px;background:rgba(40,40,48,.45)}
.nav a{position:absolute;top:47px;color:#fff;font-size:15px;text-decoration:none}
.brand{position:absolute;left:540px;top:38px;width:120px;text-align:center;color:#fff;font-size:14px;font-weight:600;line-height:1.2}
.brand .mark{margin:0 auto 6px}
.login{left:980px;top:34px;width:108px;height:48px;font-size:15px}
.hero h1{top:455px;font-size:45px;font-weight:700;color:#fff}
.hero p{top:533px;color:#fff;font-size:16px}
.order{left:533px;top:578px;width:134px;height:48px;font-size:15px}
.arrow{position:absolute;top:355px}

/* about */
.about{top:685px;height:578px}
.about-photo{left:110px;top:98px;width:425px;height:397px;border-radius:70px 70px 70px 70px;background:linear-gradient(135deg,#9c7a5a,#c8b9a4 40%,#dfe4ea 70%,#5d8fc7)}
.about h2{left:628px;top:125px;font-size:32px;font-weight:600}
.about .mark{position:absolute;left:632px;top:88px}
.about p{left:628px;top:195px;width:420px;font-size:15.5px;line-height:27.3px;color:#444}
.learn{left:628px;top:445px;width:136px;height:48px}

/* practice */
.practice{top:1263px;height:636px;background:linear-gradient(180deg,#2e5f9c,#1d4c8c 60%,#234f8e)}
.practice h2{top:100px;color:#fff;font-size:31px;font-weight:600}
.practice .center .mark{margin-top:65px}
.card{position:absolute;top:235px;width:308px;height:310px;border:2px solid #fff;border-radius:18px;text-align:center;color:#fff}
.card.active{background:var(--sky);border-color:var(--sky)}
.card .icon{position:absolute;left:94px;top:-46px;width:120px;height:90px;background:var(--sky);display:flex;align-items:center;justify-content:center}
.card.active .icon{background:#fff}
.card h3{margin-top:88px;font-size:26px;font-weight:600}
.card p{margin:16px auto 0;width:270px;font-size:15.5px;line-height:26px}
.card .chev{position:absolute;left:143px;bottom:18px}

/* testimonials */
.clients{top:1899px;height:467px}
.clients h2{top:127px;font-size:31px;font-weight:600}
.clients .center .mark{margin-top:89px}
.quote{position:absolute;top:215px;width:290px;text-align:center}
.quote p{margin-top:20px;font-size:14px;line-height:24px;color:#666}
.quote b{display:block;margin-top:18px;font-size:14.5px;color:#222}

/* newsletter */
.news{top:2366px;height:464px;background:linear-gradient(90deg,#93cbe9,#bfe3f4 45%,#7ec2e5 70%,#5fb1dd)}
.news-photo{left:820px;top:0;width:380px;height:464px;background:radial-gradient(ellipse at 45% 55%,#f4f4f2 0 22%,transparent 23%),linear-gradient(90deg,transparent,#b9dcee 80%,#e6eef2)}
.news .mark{position:absolute;left:115px;top:114px}
.news h2{left:110px;top:148px;font-size:31px;font-weight:600;color:#1f2f3f}
.field{position:absolute;top:227px;width:303px;height:50px;border-radius:25px;background:#fff;border:1px solid var(--pale);padding-left:31px;line-height:48px;font-size:15px;color:#444}
.signup{left:116px;top:331px;width:122px;height:48px;background:linear-gradient(90deg,#3f8fce,#35559a)}

/* blog */
.blog{top:2830px;height:768px}
.blog .center .mark{margin-top:88px}
.blog h2{top:124px;font-size:31px;font-weight:600}
.post{position:absolute;top:204px;width:311px;height:480px;background:#fff;box-shadow:0 3px 14px rgba(0,0,0,.1);border-bottom:3px solid var(--navy)}
.post .ph{height:215px}
.post .date{margin:31px 0 0 29px;font-size:14px;color:#777;display:flex;align-items:center;gap:8px}
.post h3{margin:14px 29px 0;font-family:"Lato",sans-serif;font-size:20px;font-weight:400;line-height:30px}
.post p{margin:12px 29px 0;font-size:14.5px;line-height:24px;color:#888}
.post a{display:inline-block;margin:8px 29px 0;font-size:15px;color:var(--sky);text-decoration:underline}

/* footer */
.foot{top:3598px;height:358px;background:var(--footer);color:#fff}
.foot-brand{left:110px;top:70px;font-family:"Poppins",sans-serif;font-size:13px;font-weight:600}
.foot-brand .mark{width:56px;height:56px;margin:0 0 10px 22px}
.social{left:110px;top:210px;display:flex;gap:8px}
.social span{width:36px;height:36px;border-radius:50%;background:#fff;display:block}
.social span:first-child{background:var(--sky)}
.vline{left:363px;top:65px;width:1px;height:175px;background:#333}
.col{position:absolute;top:72px}
.col h3{font-size:20px;font-weight:600;margin-bottom:10px}
.col li{list-style:none;font-size:15px;line-height:26px}
.col li::before{content:"»";margin-right:12px}
.contact li::before{content:none}
.contact li{display:flex;gap:10px;margin-bottom:12px;line-height:22px}
.hr{left:110px;top:272px;width:980px;height:1px;background:#333}
.copy{top:294px;font-size:15px}
</style>
</head>
<body>

<section class="hero">
  <div class="hero-photo" role="img" aria-label="Dentist treating a smiling patient in a dental chair, blue tinted"></div>
  <header class="nav">
    <a style="left:113px">Home</a>
    <a style="left:195px">About Us</a>
    <a style="left:299px">Services</a>
    <a style="left:396px">Dental Supply</a>
    <div class="brand"><span class="mark"></span>Keelpoint Dental Supply</div>
    <a style="left:724px">Blog</a>
    <a style="left:795px">Contact Us</a>
    <svg class="abs" style="left:925px;top:48px" width="18" height="18" viewBox="0 0 18 18"><circle cx="7.5" cy="7.5" r="5.5" fill="none" stroke="#2aa3e0" stroke-width="2.5"/><path d="M11.5 11.5 16 16" stroke="#2aa3e0" stroke-width="3"/></svg>
    <div class="btn login">LOG IN</div>
  </header>
  <div class="abs center" style="top:390px"><span class="mark" style="width:44px;height:44px"></span></div>
  <h1 class="abs center">A Dental Supply &amp; Medical Consulting</h1>
  <p class="abs center">Lorem ipsum dolor sit amet, consectetur adipiscing elit, sed do eiusmod tempor incididunt</p>
  <div class="btn order">ORDER NOW</div>
  <svg class="arrow" style="left:58px" width="40" height="66" viewBox="0 0 40 66"><path d="M36 3 6 33l30 30" fill="none" stroke="rgba(255,255,255,.45)" stroke-width="5"/></svg>
  <svg class="arrow" style="left:1102px" width="40" height="66" viewBox="0 0 40 66"><path d="M4 3l30 30L4 63" fill="none" stroke="#fff" stroke-width="6"/></svg>
</section>

<section class="about">
  <div class="abs about-photo" role="img" aria-label="Two pharmacy staff checking stock in a supply warehouse"></div>
  <span class="mark"></span>
  <h2 class="abs">About Keelpoint Dental Supply</h2>
  <p class="abs">Lorem ipsum dolor sit amet, consectetur adipiscing elit, sed do eiusmod tempor incididunt ut labore et dolore magna aliqua. Ut enim ad minim veniam, quis nostrud exercitation ullamco laboris nisi ut aliquip ex ea commodo consequat. Duis aute irure dolor in reprehenderit in voluptate velit esse cillum dolore eu fugiat nulla pariatur. Excepteur sint occaecat cupidatat non proident, sunt in culpa qui officia deserunt mollit anim id est laborum.</p>
  <div class="btn learn">LEARN MORE</div>
</section>

<section class="practice">
  <div class="abs center"><span class="mark"></span></div>
  <h2 class="abs center">Our Practice&nbsp; Areas</h2>
  <div class="card" style="left:110px">
    <div class="icon"><svg width="60" height="60" viewBox="0 0 60 60" fill="none" stroke="#fff" stroke-width="2.5"><path d="M30 18l10 6v12l-10 6-10-6V24z"/><circle cx="30" cy="6" r="3"/><circle cx="30" cy="54" r="3"/><circle cx="6" cy="30" r="3"/><circle cx="54" cy="30" r="3"/><circle cx="12" cy="12" r="3"/><circle cx="48" cy="48" r="3"/><circle cx="48" cy="12" r="3"/><circle cx="12" cy="48" r="3"/><path d="M30 9v9M30 42v9M9 30h11M40 30h11M14 14l8 8M46 46l-8-8M46 14l-8 8M14 46l8-8"/></svg></div>
    <h3>Distribution</h3>
    <p>Lorem ipsum dolor sit amet, consectetur adipiscing elit, sed do eiusmod tempor incididunt ut labore et dolore magna aliqua.</p>
    <svg class="chev" width="22" height="22" viewBox="0 0 22 22"><circle cx="11" cy="11" r="11" fill="var(--sky)"/><path d="M6 9l5 5 5-5" fill="none" stroke="#fff" stroke-width="2.5"/></svg>
  </div>
  <div class="card active" style="left:447px">
    <div class="icon"><svg width="64" height="64" viewBox="0 0 64 64" fill="none" stroke="#1d4c8c" stroke-width="2.5"><path d="M18 6l10 4v9c0 7-5 11-10 13-5-2-10-6-10-13v-9z"/><path d="M18 13v10M13 18h10"/><rect x="36" y="30" width="20" height="28" rx="3"/><path d="M38 24h16v6H38zM46 38v12M40 44h12"/><rect x="6" y="44" width="24" height="12" rx="6" transform="rotate(-30 18 50)"/></svg></div>
    <h3>Pharma</h3>
    <p>Lorem ipsum dolor sit amet, consectetur adipiscing elit, sed do eiusmod tempor incididunt ut labore et dolore magna aliqua.</p>
    <svg class="chev" width="22" height="22" viewBox="0 0 22 22"><circle cx="11" cy="11" r="11" fill="#fff"/><path d="M6 9l5 5 5-5" fill="none" stroke="var(--sky)" stroke-width="2.5"/></svg>
  </div>
  <div class="card" style="left:782px">
    <div class="icon"><svg width="64" height="64" viewBox="0 0 64 64" fill="none" stroke="#fff" stroke-width="2.5"><rect x="8" y="20" width="8" height="36" rx="4"/><rect x="22" y="20" width="8" height="36" rx="4"/><path d="M12 20V8M26 20V6M40 56V20l6-12 6 12v36"/><circle cx="12" cy="8" r="3"/></svg></div>
    <h3>Capital Equipment</h3>
    <p>Lorem ipsum dolor sit amet, consectetur adipiscing elit, sed do eiusmod tempor incididunt ut labore et dolore magna aliqua.</p>
    <svg class="chev" width="22" height="22" viewBox="0 0 22 22"><circle cx="11" cy="11" r="11" fill="var(--sky)"/><path d="M6 9l5 5 5-5" fill="none" stroke="#fff" stroke-width="2.5"/></svg>
  </div>
</section>

<section class="clients">
  <div class="abs center"><span class="mark"></span></div>
  <h2 class="abs center">What Our Clients Say</h2>
  <svg class="abs" style="left:66px;top:295px" width="16" height="30" viewBox="0 0 16 30"><path d="M14 2 2 15l12 13" fill="none" stroke="var(--sky)" stroke-width="2.5"/></svg>
  <svg class="abs" style="left:1118px;top:295px" width="16" height="30" viewBox="0 0 16 30"><path d="M2 2l12 13L2 28" fill="none" stroke="var(--sky)" stroke-width="2.5"/></svg>
  <div class="quote" style="left:108px"><svg width="54" height="44" viewBox="0 0 54 44" fill="var(--sky)"><path d="M2 42V26C2 12 8 4 20 2l2 5c-6 2-9 6-9 12h9v23zM30 42V26c0-14 6-22 18-24l2 5c-6 2-9 6-9 12h9v23z"/></svg><p>Loremipsumjidolorkgiusitamet, consectetur adipiscelit,seddoeiusmod temporincididunt ut labore et dolore magna aliqua.</p><b>- JOHN DOE</b></div>
  <div class="quote" style="left:455px"><svg width="54" height="44" viewBox="0 0 54 44" fill="var(--sky)"><path d="M2 42V26C2 12 8 4 20 2l2 5c-6 2-9 6-9 12h9v23zM30 42V26c0-14 6-22 18-24l2 5c-6 2-9 6-9 12h9v23z"/></svg><p>Loremipsumjidolorgiusitamet, consectetur adipiscelit,seddoeiusmod temporincididunt ut labore et dolore magna aliqua.</p><b>- JOHN DOE</b></div>
  <div class="quote" style="left:803px"><svg width="54" height="44" viewBox="0 0 54 44" fill="var(--sky)"><path d="M2 42V26C2 12 8 4 20 2l2 5c-6 2-9 6-9 12h9v23zM30 42V26c0-14 6-22 18-24l2 5c-6 2-9 6-9 12h9v23z"/></svg><p>Loremipsumjidolorgiusitamet, consectetur adipiscelit,seddoeiusmod temporincididunt ut labore et dolore magna aliqua.</p><b>- JOHN DOE</b></div>
</section>

<section class="news">
  <div class="abs news-photo" role="img" aria-label="White model tooth beside dental instruments and a face mask"></div>
  <span class="mark"></span>
  <h2 class="abs">Subscribe To Our Newsletter</h2>
  <div class="field" style="left:110px">Name</div>
  <div class="field" style="left:430px">Email</div>
  <div class="btn signup">SIGN UP</div>
</section>

<section class="blog">
  <div class="abs center"><span class="mark"></span></div>
  <h2 class="abs center">Our Blog</h2>
  <svg class="abs" style="left:66px;top:445px" width="16" height="30" viewBox="0 0 16 30"><path d="M14 2 2 15l12 13" fill="none" stroke="var(--sky)" stroke-width="2.5"/></svg>
  <svg class="abs" style="left:1118px;top:445px" width="16" height="30" viewBox="0 0 16 30"><path d="M2 2l12 13L2 28" fill="none" stroke="var(--sky)" stroke-width="2.5"/></svg>
  <article class="post" style="left:110px">
    <div class="ph" role="img" aria-label="Store shelves stocked with toothbrushes and toothpaste" style="background:linear-gradient(180deg,#c7d3e3,#d85a5a 45%,#e9eef3 75%,#b94b4b)"></div>
    <div class="date"><svg width="16" height="16" viewBox="0 0 16 16"><circle cx="8" cy="8" r="7" fill="none" stroke="var(--sky)" stroke-width="1.6"/><path d="M8 4v4h3" fill="none" stroke="var(--sky)" stroke-width="1.6"/></svg>December 20,2021</div>
    <h3>Sed ut perspiciatis unde omnis iste natus</h3>
    <p>Lorem ipsum dolor sit amet, elit, sed do eiusmod tempor incididunt ut labore et dolore magna aliqua.</p>
    <a>Learn More</a>
  </article>
  <article class="post" style="left:444px">
    <div class="ph" role="img" aria-label="Pharmacy aisle with shelves of medicine boxes" style="background:linear-gradient(90deg,#dfe6ee,#f5f7f9 50%,#cfd9e4)"></div>
    <div class="date"><svg width="16" height="16" viewBox="0 0 16 16"><circle cx="8" cy="8" r="7" fill="none" stroke="var(--sky)" stroke-width="1.6"/><path d="M8 4v4h3" fill="none" stroke="var(--sky)" stroke-width="1.6"/></svg>December 20,2021</div>
    <h3>Sed ut perspiciatis unde omnis iste natus</h3>
    <p>Lorem ipsum dolor sit amet, elit, sed do eiusmod tempor incididunt ut labore et dolore magna aliqua.</p>
    <a>Learn More</a>
  </article>
  <article class="post" style="left:778px">
    <div class="ph" role="img" aria-label="Medical supply storeroom with metal shelving" style="background:linear-gradient(90deg,#9aa7b4,#e4eaf0 50%,#a9b4bf)"></div>
    <div class="date"><svg width="16" height="16" viewBox="0 0 16 16"><circle cx="8" cy="8" r="7" fill="none" stroke="var(--sky)" stroke-width="1.6"/><path d="M8 4v4h3" fill="none" stroke="var(--sky)" stroke-width="1.6"/></svg>December 20,2021</div>
    <h3>Sed ut perspiciatis unde omnis iste natus</h3>
    <p>Lorem ipsum dolor sit amet, elit, sed do eiusmod tempor incididunt ut labore et dolore magna aliqua.</p>
    <a>Learn More</a>
  </article>
</section>

<footer class="foot">
  <div class="abs foot-brand"><span class="mark"></span>Keelpoint Dental Supply</div>
  <div class="abs social" aria-label="Social media links"><span></span><span></span><span></span><span></span></div>
  <div class="abs vline"></div>
  <div class="col" style="left:420px"><h3>Quick Links</h3><ul><li>Home</li><li>About Us</li><li>Services</li><li>Dental Supply</li><li>Blog</li><li>Contact Us</li></ul></div>
  <div class="col" style="left:630px"><h3>Our Company</h3><ul><li>Terms &amp; Conditions</li><li>Privacy Policy</li><li>About Us</li><li>Support</li></ul></div>
  <div class="col contact" style="left:854px"><h3>Contact us</h3><ul>
    <li><svg width="14" height="20" viewBox="0 0 14 20"><path d="M7 0C3 0 0 3 0 7c0 5 7 13 7 13s7-8 7-13c0-4-3-7-7-7z" fill="#fff"/><circle cx="7" cy="7" r="2.5" fill="var(--footer)"/></svg><span>Lorem ipsum dolor sit<br>amet, consectetur adipiscing</span></li>
    <li><svg width="14" height="16" viewBox="0 0 16 16"><path d="M3 1l3 3-2 2c1 2 3 4 5 5l2-2 3 3-2 3C7 15 1 9 1 3z" fill="#fff"/></svg><span>1+ (555) 014 2290</span></li>
    <li><svg width="16" height="14" viewBox="0 0 16 12"><rect width="16" height="12" rx="1" fill="#fff"/><path d="M1 1l7 6 7-6" fill="none" stroke="var(--footer)" stroke-width="1.5"/></svg><span>info@keelpointdental.com</span></li>
  </ul></div>
  <div class="abs hr"></div>
  <div class="abs center copy">©Copyrights 2023 Keelpoint Dental Supply &nbsp;|&nbsp;&nbsp; All Rights Reserved</div>
</footer>

</body>
</html>
```